Valdane Companies Business Card Design

We need a new business card for our Private Equity Real Estate Development firm, “Valdane” and our EB-5 regional center “Thornmere Regional Center” on one card. We prefer a design that is simple, elegant, and represents the luxury products we design and build as well as the financial security and stability our successful history has produced. We are an industry leader in our field and 3rd generation family business that has evolved into an institutional quality investment platform. Considered design size is standard business card dimensions (3.5 x 2 inches with an additional 1/8 inch space for design elements or backgrounds that extend beyond the finished size of your piece.

Target Market(s)

• High net worth individuals
• Highly skilled technical workers and physicians in the US seeking investment-based immigration opportunities
• Sophisticated private equity investors
• Intermediary partners include domestic attorneys and investment brokers, as well as international agent networks
• US real estate developers

Industry/Entity Type

Finance

Contact Information for Business Card

(Providing placeholder info for personal information, please design for longer character spaces, longer names and addresses etc..)
• Logo for Valdane
• Logo for Thornmere Regional Center
• Full name: Marcus Valdane
• Job title: CEO
• Email address: mvaldane@valdanecompanies.com
• Cell phone number: +1.555.314.2287
• Office number +1.555.628.4410
• Office address: Larkfield Court 5, 4817 Vista Orilla, Elmhaven, CA.
• Website: www.valdanecompanies.com

Font styles to use
Serif
Sans Serif

Colors
ec1f27
ffffff
000000

Requirements
Must have
• • Logo for Valdane
• • Logo for Thornmere Regional Center
• - Use rounded corners
• (See .ai file included for logos)
Nice to have
• • Simple, elegant design
• • Aesthetically compatible with our website design (www.valdanecompanies.com)
• • Color palette including but not limited to white, black, and red (as per logos)
Should not have
• - Not too much red color
• - Do not stack both logos on top of each other

```html
<!DOCTYPE html>
<html lang="en">
<head>
<meta charset="utf-8">
<title>Valdane Capital Business Card</title>
<link rel="stylesheet" href="https://fonts.googleapis.com/css2?family=Cinzel:wght@600&family=PT+Sans:wght@400;700&display=swap">
<style>
  :root {
    --backdrop: #8c8c8c;
    --card-light: #efefef;
    --ink-dark: #2b2b2b;
    --band-dark: #2e2e2e;
    --brand-red: #a51c30;
    --card-back: #3a3a3a;
    --pattern-tone: #353535;
    --text-light: #ffffff;
    --mark-grey: #c9c9c9;
    --rule-red: rgba(255,255,255,0.35);
  }
  * { margin: 0; padding: 0; box-sizing: border-box; }
  html, body { width: 1200px; height: 1200px; overflow: hidden; }
  body {
    background: var(--backdrop);
    position: relative;
    font-family: "PT Sans", Arial, sans-serif;
  }
  .card {
    position: absolute;
    top: 310px;
    height: 594px;
    border-radius: 6px;
    overflow: hidden;
  }
  .card--front { left: 234px; width: 364px; background: var(--card-light); }
  .card--back { left: 628px; width: 368px; background: var(--card-back); }

  .front-brand {
    height: 302px;
    display: flex;
    align-items: center;
    justify-content: center;
    gap: 12px;
    padding-top: 40px;
  }
  .brand-square {
    width: 28px; height: 28px;
    background: var(--ink-dark);
  }
  .brand-name {
    font-family: "Cinzel", Georgia, serif;
    font-weight: 600;
    font-size: 24px;
    color: var(--ink-dark);
    letter-spacing: 0.5px;
  }
  .front-band { height: 18px; background: var(--band-dark); }
  .front-contact {
    height: 274px;
    background: var(--brand-red);
    color: var(--text-light);
    text-align: center;
    padding-top: 26px;
  }
  .person-name {
    font-family: "Cinzel", Georgia, serif;
    font-weight: 600;
    font-size: 23px;
    line-height: 1.1;
    letter-spacing: 0.3px;
  }
  .person-title { font-size: 16px; margin-top: 3px; }
  .rule {
    width: 226px; height: 1px;
    background: var(--rule-red);
    margin: 8px auto 9px;
  }
  .contact-list { list-style: none; font-size: 16px; line-height: 21.5px; }
  .contact-list b { font-weight: 700; }
  .address { font-size: 16px; line-height: 21.5px; }

  .back-pattern {
    position: absolute;
    left: 0; top: 0;
    width: 368px; height: 594px;
    background: var(--pattern-tone);
  }
  .center-brand {
    position: absolute;
    left: 0; right: 0;
    top: 498px;
    display: flex;
    align-items: center;
    justify-content: center;
    gap: 10px;
  }
  .center-square { width: 26px; height: 26px; background: var(--mark-grey); }
  .center-name {
    font-family: "Cinzel", Georgia, serif;
    font-weight: 600;
    font-size: 15px;
    color: var(--mark-grey);
    letter-spacing: 0.3px;
  }
</style>
</head>
<body>
  <section class="card card--front" aria-label="Card front">
    <div class="front-brand">
      <span class="brand-square"></span>
      <span class="brand-name">VALDANE CAPITAL</span>
    </div>
    <div class="front-band"></div>
    <div class="front-contact">
      <h1 class="person-name">MARCUS VALDANE</h1>
      <p class="person-title">CEO</p>
      <div class="rule"></div>
      <ul class="contact-list">
        <li><b>P:</b> +1.555.314.2287</li>
        <li><b>M:</b> +1.555.628.4410</li>
        <li><b>E:</b> mvaldane@valdanecompanies.com</li>
        <li><b>W:</b> www.valdanecompanies.com</li>
      </ul>
      <div class="rule"></div>
      <p class="address">Larkfield Court 5, 4817 Vista<br>Orilla, Elmhaven, CA</p>
    </div>
  </section>

  <section class="card card--back" aria-label="Card back">
    <div class="back-pattern" role="img" aria-label="Faint repeated monogram pattern covering the card back"></div>
    <div class="center-brand">
      <span class="center-square"></span>
      <span class="center-name">THORNMERE REGIONAL CENTER</span>
    </div>
  </section>
</body>
</html>
```